Security based company delivering High Risk Training to Law Enforcement Agencies Worldwide.

We need a Web design for a company doing business in Washington D.C. We deliver High Risk Training to Law Enforcement Agencies throughout the world. Our focus is on Improvised Explosive Devices. We train Bomb Technicians and First Responders in all aspects relating to bombings and criminal incidents globally.
Updates

Reason: We have uploaded our logo. Thank you.

Target Market(s)

Military and Law Enforcement Personnel from around the world.

Industry/Entity Type

Business

Requirements
Should not have
• Do not include cartoon like characters.

```html
<!DOCTYPE html>
<html lang="en">
<head>
<meta charset="utf-8">
<title>Ironline Tactical</title>
<link href="https://fonts.googleapis.com/css2?family=Roboto:wght@300;400;500;700&family=Roboto+Slab:wght@300;400;700&display=swap" rel="stylesheet">
<style>
:root{
  --coral:#f47a72;
  --coral-light:#f9938b;
  --ink:#333;
  --muted:#666;
  --dark:#3f4553;
  --footer:#eeeded;
  --white:#fff;
}
*{box-sizing:border-box;margin:0;padding:0}
html,body{width:1124px;height:1200px;overflow:hidden}
body{position:relative;background:#fff;font-family:'Roboto',sans-serif;color:var(--ink)}
.abs{position:absolute}
.header-band{left:0;top:0;width:1124px;height:438px;border-top:3px solid #222;
  background:linear-gradient(90deg,#7d7774 0%,#6b6769 30%,#66646a 60%,#7e7670 100%)}
.below-band{left:0;top:438px;width:1124px;height:110px;background:linear-gradient(#f3f3f3,#fff)}
.brand{left:163px;top:29px;font-weight:700;font-size:24px;color:var(--white);letter-spacing:.3px}
.phone{left:816px;top:29px;display:flex;align-items:center;gap:10px;color:var(--white);font-size:18px;letter-spacing:.5px}
.nav{left:164px;top:79px;width:801px;height:47px;display:flex;background:linear-gradient(#fff,#e9eef3);border-bottom:3px solid #dfe8f0}
.nav a{display:flex;align-items:center;justify-content:center;font-size:13px;color:#333;text-decoration:none;border-right:1px solid #d6dbe0;height:100%}
.nav a.active{background:var(--coral);color:#fff}
.hero{left:164px;top:126px;width:801px;height:365px;background:linear-gradient(180deg,#a7a3a4 0%,#c9bfb5 40%,#b8a78f 75%,#c8ac8a 100%)}
.hero-shadow{left:200px;top:488px;width:730px;height:40px;background:radial-gradient(ellipse at top,rgba(0,0,0,.18),rgba(0,0,0,0) 70%)}
.hero-title{left:492px;top:222px;font-family:'Roboto Slab',serif;font-weight:700;font-size:34px;line-height:41px;color:#fff;text-shadow:0 0 2px #555,1px 1px 3px rgba(0,0,0,.6);white-space:nowrap}
.hero-btn{left:506px;top:325px;width:141px;height:43px;background:linear-gradient(#2a2a2a,#000);border-radius:3px;color:#fff;font-size:18px;display:flex;align-items:center;justify-content:center;box-shadow:0 2px 3px rgba(0,0,0,.4)}
.dots{left:873px;top:464px;display:flex;gap:7px}
.dots span{width:9px;height:9px;border-radius:50%;background:#fff}
.dots span.on{background:var(--coral)}
.welcome-frame{left:167px;top:538px;width:238px;height:162px;border:3px solid #fff;box-shadow:0 1px 4px rgba(0,0,0,.35);background:linear-gradient(#a5a3a4,#c5b49b 60%,#bfa582)}
.welcome-title{left:423px;top:539px;font-family:'Roboto Slab',serif;font-weight:300;font-size:18px;color:var(--coral);white-space:nowrap}
.welcome-text{left:424px;top:567px;width:546px;font-size:12.6px;line-height:22.5px;color:#333;letter-spacing:-.05px}
.btn-read{left:423px;top:666px;width:93px;height:29px;background:var(--coral-light);color:#fff;font-size:12px;display:flex;align-items:center;justify-content:center;border-radius:2px}
.sec-title{font-family:'Roboto Slab',serif;font-weight:300;font-size:15px;color:var(--coral)}
.circ{width:16px;height:16px}
.news-item{left:161px;display:flex;gap:9px}
.date{width:42px;height:47px;background:#fff;border:1px solid #ddd;box-shadow:0 0 0 4px #f2f2f2;text-align:center}
.date b{display:block;font-size:14px;font-weight:500;line-height:30px;border-bottom:1px solid #e5e5e5}
.date small{display:block;font-size:8px;color:#888;line-height:15px;background:#f1f1f1}
.news-item h4{font-size:11px;font-weight:400;margin-top:1px;white-space:nowrap}
.news-item p{font-size:9.5px;color:#444;margin-top:10px;white-space:nowrap}
.news-sep{left:166px;top:864px;width:197px;border-top:1px dotted #777}
.vline{left:384px;top:759px;width:1px;height:184px;background:#ddd}
.card{top:795px;width:177px;height:146px;background:#fff;border-bottom:2px solid #ddd;box-shadow:0 1px 2px rgba(0,0,0,.12);text-align:center}
.card .img{height:101px}
.card h5{font-size:10.5px;font-weight:400;color:var(--coral);margin-top:9px}
.card p{font-size:9.5px;color:#555;margin-top:5px}
.footer{left:0;top:990px;width:1124px;height:141px;background:var(--footer)}
.fcol{top:1014px}
.fcol h6{font-size:12.5px;font-weight:400;color:var(--coral);margin-bottom:13px}
.fcol li{list-style:none;font-size:12.5px;color:#333;line-height:21.3px;white-space:nowrap}
.bottom{left:0;top:1131px;width:1124px;height:69px;background:var(--dark)}
.copy{left:164px;top:1160px;font-size:9.5px;color:#fff}
.social{top:1147px;width:34px;height:34px;border:1px solid #2e323d;background:#3a3f4c;border-radius:2px}
</style>
</head>
<body>
<div class="abs header-band" role="img" aria-label="Blurred photo of a desert training ground with a suspicious package"></div>
<div class="abs below-band"></div>

<div class="abs brand">IRONLINE TACTICAL</div>
<div class="abs phone">
  <svg width="21" height="21" viewBox="0 0 24 24"><circle cx="12" cy="12" r="11" fill="none" stroke="#f47a72" stroke-width="1.6"/><path d="M8 6.5l2 2.3-1.2 1.4c.7 1.7 2.2 3.3 4 4l1.4-1.2 2.3 2-1.3 1.7c-3.5-.4-7.4-4.3-7.8-7.8z" fill="none" stroke="#f47a72" stroke-width="1.4"/></svg>
  <span>0201 555 0148</span>
</div>

<nav class="abs nav">
  <a class="active" style="width:85px">HOME</a>
  <a style="width:113px">ABOUT US</a>
  <a style="width:115px">SERVICES</a>
  <a style="width:112px">TRAINING</a>
  <a style="width:128px">TECHNICIAN</a>
  <a style="width:108px">BOMBING</a>
  <a style="width:140px;border-right:0">CONTACT US</a>
</nav>

<div class="abs hero" role="img" aria-label="Photo of a bomb technician in a protective suit working near a stop sign and a wall"></div>
<div class="abs hero-shadow"></div>
<div class="abs hero-title">HIGH RISK TRAINING<br>TO LAW ENFORCEMENT</div>
<div class="abs hero-btn">VIEW MORE</div>
<div class="abs dots"><span></span><span></span><span class="on"></span><span></span><span></span></div>

<div class="abs welcome-frame" role="img" aria-label="Photo of a controlled explosion in the desert"></div>
<h2 class="abs welcome-title">WELCOME TO IRONLINE TACTICAL</h2>
<p class="abs welcome-text">Lorem Ipsum is simply dummy text of the printing and typesetting industry. Lorem Ipsum has been the industry's standard dummy text ever since the 1500s, when an unknown printer took a galley of type and scrambled it to make a type specimen book. It has survived not only five centuries, but also the leap into electronic typesetting, remaining essentially unchanged</p>
<div class="abs btn-read">READ MORE</div>

<h3 class="abs sec-title" style="left:164px;top:764px">LATEST NEWS</h3>
<svg class="abs circ" style="left:348px;top:764px" viewBox="0 0 16 16"><circle cx="8" cy="8" r="7" fill="none" stroke="#222" stroke-width="1.4"/><path d="M7 5l3 3-3 3" fill="none" stroke="#222" stroke-width="1.4"/></svg>

<div class="abs news-item" style="top:804px">
  <div class="date"><b>20</b><small>mar</small></div>
  <div><h4>NEWS HEADLINE HERE</h4><p>Lorem ipsum dolor sit amet, consec-</p></div>
</div>
<div class="abs news-sep"></div>
<div class="abs news-item" style="top:880px">
  <div class="date"><b>20</b><small>mar</small></div>
  <div><h4>NEWS HEADLINE HERE</h4><p>Lorem ipsum dolor sit amet, consec-</p></div>
</div>

<div class="abs vline"></div>

<h3 class="abs sec-title" style="left:402px;top:763px">WE TRAIN</h3>
<svg class="abs circ" style="left:929px;top:764px" viewBox="0 0 16 16"><circle cx="8" cy="8" r="7" fill="none" stroke="#222" stroke-width="1.4"/><path d="M9 5l-3 3 3 3" fill="none" stroke="#222" stroke-width="1.4"/></svg>
<svg class="abs circ" style="left:947px;top:764px" viewBox="0 0 16 16"><circle cx="8" cy="8" r="7" fill="none" stroke="#222" stroke-width="1.4"/><path d="M7 5l3 3-3 3" fill="none" stroke="#222" stroke-width="1.4"/></svg>

<div class="abs card" style="left:405px">
  <div class="img" role="img" aria-label="Photo of a car engulfed in an explosion" style="background:linear-gradient(90deg,#b9a894,#d2c7bb 45%,#f0a54a 80%,#e7b57a)"></div>
  <h5>BOMB TECHNICIANS</h5><p>Lorem ipsum dolor sit amet</p>
</div>
<div class="abs card" style="left:595px">
  <div class="img" role="img" aria-label="Photo of a sand blast cloud from a detonation" style="background:linear-gradient(#b7a793,#cdb89c 50%,#a98f72)"></div>
  <h5>RELATING TO BOMBINGS</h5><p>Lorem ipsum dolor sit amet</p>
</div>
<div class="abs card" style="left:786px">
  <div class="img" role="img" aria-label="Photo of a car blast with black smoke" style="background:linear-gradient(90deg,#c4bcb3,#8a8580 50%,#3a3533 70%,#c89265)"></div>
  <h5>CRIMINAL INCIDENTS</h5><p>Lorem ipsum dolor sit amet</p>
</div>

<footer class="abs footer"></footer>
<div class="abs fcol" style="left:165px"><h6>COMPANY</h6><ul><li>About us</li><li>Services</li><li>Presentation</li></ul></div>
<div class="abs fcol" style="left:309px"><h6>SPECIALISTS</h6><ul><li>Commercial</li><li>Residential</li><li>Luxury</li></ul></div>
<div class="abs fcol" style="left:448px"><h6>ADVICE</h6><ul><li>FAQs</li><li>Support</li></ul></div>
<div class="abs fcol" style="left:593px"><h6>AGENCIES</h6><ul><li>Sign Up</li><li>Forums</li><li>Promotions</li></ul></div>
<div class="abs fcol" style="left:731px"><h6>CONTACT US</h6><ul><li>412 Harlow Street, Arden, AR7 2KD</li><li>Phone: +1 800 555 0172</li><li>E-mail: info@ironlinetactical.org</li></ul></div>

<div class="abs bottom"></div>
<div class="abs copy">Copy Right © 2014. All rights reserved.</div>
<div class="abs social" style="left:735px" aria-label="Social link"></div>
<div class="abs social" style="left:799px" aria-label="Social link"></div>
<div class="abs social" style="left:863px" aria-label="Social link"></div>
<div class="abs social" style="left:927px" aria-label="Social link"></div>
</body>
</html>
```